wealth management firm, professional group, new model

we have a logo that works but we need a card, white background using our colors...clean look

our tag line if can be used in

Guiding You From Saver to Steward

```html
<!DOCTYPE html>
<html lang="en">
<head>
<meta charset="utf-8">
<title>Arcova Wealth Group – Business Card</title>
<link rel="stylesheet" href="https://fonts.googleapis.com/css2?family=Montserrat:wght@400;500;700&display=swap">
<style>
  :root {
    --navy: #14264a;
    --card: #ffffff;
    --backdrop: #f1ecdf;
    --edge: #e4ddcc;
  }
  * { box-sizing: border-box; margin: 0; padding: 0; }
  html, body {
    width: 1200px;
    height: 896px;
    overflow: hidden;
    background: var(--backdrop);
    font-family: "Montserrat", Arial, sans-serif;
    color: var(--navy);
  }
  .sheet {
    width: 1200px;
    height: 896px;
    display: flex;
    align-items: center;
    justify-content: center;
    gap: 40px;
  }
  .card {
    width: 520px;
    height: 297px;
    background: var(--card);
    border: 1px solid var(--edge);
    box-shadow: 0 6px 18px rgba(20, 38, 74, 0.08);
    display: flex;
    flex-direction: column;
    align-items: center;
    text-align: center;
  }

  /* Front: advisor details */
  .card--front { padding: 38px 40px 34px; justify-content: space-between; }
  .advisor-name {
    font-weight: 700;
    font-size: 30px;
    letter-spacing: 0.06em;
    line-height: 1;
  }
  .advisor-title {
    font-weight: 400;
    font-size: 17px;
    margin-top: 8px;
  }
  .front-mark {
    display: flex;
    align-items: center;
    gap: 10px;
    font-weight: 500;
    font-size: 18px;
    letter-spacing: 0.08em;
  }
  .mark-square {
    width: 10px;
    height: 10px;
    background: var(--navy);
  }
  .contact {
    font-style: normal;
    font-size: 14px;
    line-height: 1.5;
  }

  /* Back: firm name and tagline */
  .card--back { padding: 44px 40px 36px; justify-content: center; }
  .firm-name {
    display: flex;
    align-items: center;
    gap: 14px;
    font-weight: 500;
    font-size: 30px;
    letter-spacing: 0.08em;
    line-height: 1;
  }
  .divider {
    width: 120px;
    height: 2px;
    background: var(--navy);
    margin: 26px 0 20px;
  }
  .tagline {
    font-weight: 700;
    font-size: 14px;
    letter-spacing: 0.04em;
    text-transform: uppercase;
  }
</style>
</head>
<body>
  <main class="sheet">
    <section class="card card--front" aria-label="Business card front">
      <header>
        <h1 class="advisor-name">JORDAN HALE</h1>
        <p class="advisor-title">Senior Wealth Advisor</p>
      </header>
      <div class="front-mark"><span class="mark-square"></span>ARCOVA WEALTH GROUP</div>
      <address class="contact">
        jordan@arcovawealth.com | +1 (555) 010-4821<br>
        arcovawealth.com
      </address>
    </section>

    <section class="card card--back" aria-label="Business card back">
      <div class="firm-name"><span class="mark-square"></span>ARCOVA WEALTH GROUP</div>
      <div class="divider"></div>
      <p class="tagline">Guiding You From Saver to Steward</p>
    </section>
  </main>
</body>
</html>
```